Exciting opportunity to create logo and a label for our natural health brand.

About us

We are a customer centric health supplement brand who believes in natural medicine and high quality ingredients. We take a holistic approach to healthcare, with an eastern philosophy. We believe in being partners with our customers in their health care journey and are invested in their well being.

Our brand philosophy and values are attached (see Vorna philosophy.png). Our personality traits are:

- Natural
- Fresh
- Modern
- Balanced (in a holistic sense)

Task breakdown

1. Design a fresh feeling logo for us
- We want it to represent our values and high quality ingredients. We would like the quality of the product to be reflected in the branding and have a high end feel.
- Logo text must include Vorna Health Sciences
- We want the Vorna to be the focus of the logo (see uploaded image Vorna logo example.png)
The logo does not have to follow this layout, but we just want the Vorna to stand out. Feel free to use your creative license on this!

2. Create an attractive label to go on the supplement bottle
- The designs need to be eye catching, give a sense of high end ingredients and natural products and tie in with the logo to give a joined up feel.
- We are selling our products online and need them to really stand out from the competition.
- See examples of labels and packaging we like (1 -7 label design).

The initial label we would like you to design would be for our product Calm Drift. It is a product that assists in the management of Anxiety and stress. The label will appear on the bottle that holds the capsules for this supplement, see uploaded files (Example plain bottles.png). The bottles may be white as the picture shows or dark blue recyclable plastic or dark brown glass . We don't have the exact dimensions of the bottle yet, but I will follow up with these.

The label needs to include the following things:
1. The logo
2. The name of the product
3. The product is to help with the relief of Anxiety and Stress
4. Number of capsules the bottle contains
5. The back of the label should have
i) The ingredients
ii) Dosage
iii) Directions of use

Please use placeholder text where needed.

We look forward to seeing your design. Thank you.

```html
<!DOCTYPE html>
<html lang="en">
<head>
<meta charset="utf-8">
<title>Vorna Health Sciences – Calm Drift label</title>
<link href="https://fonts.googleapis.com/css2?family=Montserrat:wght@400;600;700&family=Raleway:wght@300;400&family=Archivo+Black&family=Roboto:wght@400;700;900&display=swap" rel="stylesheet">
<style>
  :root{
    --ink:#111;
    --green:#1f9a12;
    --label-green:#e8f2da;
    --label-cream:#f6efd6;
    --orange:#f08a1c;
    --yellow:#f4b21b;
    --band-white:#fffdf6;
    --page:#ffffff;
  }
  *{box-sizing:border-box;margin:0;padding:0}
  html,body{width:1079px;height:1200px;overflow:hidden;background:var(--page)}
  body{font-family:"Montserrat",sans-serif;color:var(--ink);position:relative}

  .brand{position:absolute;left:0;top:20px;width:1079px;height:220px;display:flex;align-items:center;justify-content:center;gap:26px}
  .brand-dot{width:120px;height:120px;border:10px solid var(--green);border-radius:50%}
  .brand-text{display:flex;flex-direction:column}
  .brand-name{font-family:"Montserrat",sans-serif;font-weight:600;font-size:110px;line-height:1;color:var(--ink)}
  .brand-sub{font-family:"Montserrat",sans-serif;font-weight:600;font-size:34px;letter-spacing:1px;color:var(--ink);margin-top:6px}

  .label{position:absolute;left:20px;width:1039px;height:450px;overflow:hidden}
  .label--green{top:262px;background:var(--label-green)}
  .label--cream{top:732px;background:var(--label-cream)}
  .label-texture{position:absolute;left:300px;top:60px;width:420px;height:300px;border-radius:50%;
    background:radial-gradient(ellipse at center,rgba(255,255,255,.75),rgba(255,255,255,0) 70%)}
  .swoosh{position:absolute;inset:0;width:100%;height:100%}

  .back-copy{position:absolute;left:26px;top:16px;width:250px;z-index:2}
  .back-copy h3{font-family:"Montserrat",sans-serif;font-weight:700;font-size:15px;margin:0 0 4px}
  .back-copy p{font-family:"Montserrat",sans-serif;font-size:11.6px;line-height:1.45;margin-bottom:14px}
  .about{position:absolute;left:26px;top:290px;width:230px;z-index:2;font-family:"Raleway",sans-serif;font-weight:400;color:#333}
  .about h4{font-weight:400;font-size:17px;margin-bottom:2px}
  .about p{font-size:17px;line-height:1.35}

  .label-brand{position:absolute;left:420px;top:38px;display:flex;align-items:center;gap:8px;z-index:2}
  .label-brand .dot{width:34px;height:34px;border:3px solid var(--green);border-radius:50%}
  .label-brand .name{font-family:"Montserrat",sans-serif;font-weight:600;font-size:36px;line-height:1}
  .label-brand .sub{font-family:"Montserrat",sans-serif;font-weight:600;font-size:11px;margin-top:2px}

  .product{position:absolute;left:300px;width:400px;top:230px;text-align:center;z-index:2}
  .product-name{font-family:"Archivo Black",sans-serif;font-size:40px;letter-spacing:2px;line-height:1}
  .product-claim{font-family:"Raleway",sans-serif;font-weight:300;font-size:21px;color:var(--green);margin-top:8px}

  .count{position:absolute;left:300px;width:400px;bottom:4px;text-align:center;font-family:"Montserrat",sans-serif;font-weight:600;font-size:25px;letter-spacing:1px;z-index:2}

  .facts{position:absolute;left:820px;top:16px;width:205px;border:1.5px solid var(--ink);padding:4px 6px;background:transparent;font-family:"Roboto",sans-serif;font-size:8.2px;line-height:1.55;z-index:2}
  .facts h5{font-family:"Roboto",sans-serif;font-weight:900;font-size:19px;line-height:1.1}
  .facts .row{display:flex;justify-content:space-between;border-bottom:.5px solid #555}
  .facts .row.indent{padding-left:12px}
  .facts .thick{border-bottom:5px solid var(--ink)}
  .facts .mid{border-bottom:2.5px solid var(--ink)}
  .facts b{font-weight:700}
  .facts .dv{justify-content:flex-end;font-weight:700;font-size:6.5px}
  .facts .note{font-size:6.4px;line-height:1.3;padding-top:3px;border:none}
</style>
</head>
<body>

<header class="brand">
  <span class="brand-dot"></span>
  <div class="brand-text">
    <span class="brand-name">Vorna</span>
    <span class="brand-sub">HEALTH SCIENCES</span>
  </div>
</header>

<section class="label label--green" aria-label="Calm Drift label, green version">
  <div class="label-texture" role="img" aria-label="Soft dotted light pattern"></div>
  <svg class="swoosh" viewBox="0 0 1039 450" preserveAspectRatio="none" aria-hidden="true">
    <defs>
      <linearGradient id="orangeFade" x1="0" x2="1">
        <stop offset="0" stop-color="#f08a1c"/><stop offset=".6" stop-color="#f5a623"/><stop offset="1" stop-color="#f08a1c" stop-opacity=".3"/>
      </linearGradient>
    </defs>
    <path d="M0 330 C300 300 620 300 1039 320 L1039 345 C620 330 300 345 0 380Z" fill="url(#orangeFade)"/>
    <path d="M0 380 C300 348 620 336 1039 345 L1039 385 C620 378 300 390 0 405Z" fill="#fffdf6"/>
    <path d="M0 405 C300 392 620 380 1039 385 L1039 450 L0 450Z" fill="#f4b21b"/>
  </svg>

  <div class="back-copy">
    <h3>DIRECTIONS OF USE</h3>
    <p>Lorem ipsum dolor sit amet, consectetuer adipiscing elit, sed diam nonummy nibh euismod tincidunt ut laoreet dolore magna aliquam erat volutpat. Ut wisi enim ad minim veniam, quis nostrud exerci tation ullamcorper suscipit lobortis</p>
    <h3>INGREDIENTS</h3>
    <p>Lorem ipsum dolor sit amet, consectetuer adipiscing elit, sed diam nonummy nibh euismod tincidunt ut laoreet dolore magna</p>
  </div>
  <div class="about">
    <h4>ABOUT COMPANU</h4>
    <p>adipiscing elit, sed diam nonummy nibh euismod tincidunt ut laoreet dolore magna aliquam erat</p>
  </div>

  <div class="label-brand">
    <span class="dot"></span>
    <div><div class="name">Vorna</div><div class="sub">HEALTH SCIENCES</div></div>
  </div>

  <div class="product">
    <div class="product-name">CALM DRIFT</div>
    <div class="product-claim">ANXIETY AND STRESS</div>
  </div>

  <div class="facts">
    <h5>Nutrition Facts</h5>
    <div class="row" style="border:none"><span>Serving Size</span><span>...g</span></div>
    <div class="row thick"><span>Servings Per Container</span><span></span></div>
    <div class="row"><b>Amount Per Serving</b></div>
    <div class="row mid"><span><b>Calories</b> ....</span><span>Calories from Fat ...</span></div>
    <div class="row dv"><span>% Daily Value*</span></div>
    <div class="row"><span><b>Total Fat</b> ...g</span><b>...%</b></div>
    <div class="row indent"><span>Saturated Fat ...g</span><b>...%</b></div>
    <div class="row indent"><span><i>Trans</i> Fat ...g</span></div>
    <div class="row"><span><b>Cholestrol</b> ...mg</span><b>...%</b></div>
    <div class="row"><span><b>Sodium</b> ...mg</span><b>...%</b></div>
    <div class="row"><span><b>Total Carbohydrate</b> ...g</span><b>...%</b></div>
    <div class="row indent"><span>Dietary Fiber ...g</span><b>...%</b></div>
    <div class="row indent"><span>Sugars ...g</span></div>
    <div class="row thick"><span><b>Protein</b> ...g</span></div>
    <div class="row"><span>Vitamin A</span><b>...%</b></div>
    <div class="row"><span>Vitamin C</span><b>...%</b></div>
    <div class="row"><span>Calcium</span><b>...%</b></div>
    <div class="row mid"><span>Iron</span><b>...%</b></div>
    <div class="row note"><span>*Percent Daily Values are based on a 2,000 calorie diet. Your Daily Values may be higer or lower depending on your calorie needs.</span></div>
  </div>

  <div class="count">60 CAPSULES</div>
</section>

<section class="label label--cream" aria-label="Calm Drift label, cream version">
  <div class="label-texture" role="img" aria-label="Soft dotted light pattern"></div>
  <svg class="swoosh" viewBox="0 0 1039 450" preserveAspectRatio="none" aria-hidden="true">
    <path d="M0 330 C300 300 620 300 1039 320 L1039 345 C620 330 300 345 0 380Z" fill="url(#orangeFade)"/>
    <path d="M0 380 C300 348 620 336 1039 345 L1039 385 C620 378 300 390 0 405Z" fill="#fffdf6"/>
    <path d="M0 405 C300 392 620 380 1039 385 L1039 450 L0 450Z" fill="#f4b21b"/>
  </svg>

  <div class="back-copy">
    <h3>DIRECTIONS OF USE</h3>
    <p>Lorem ipsum dolor sit amet, consectetuer adipiscing elit, sed diam nonummy nibh euismod tincidunt ut laoreet dolore magna aliquam erat volutpat. Ut wisi enim ad minim veniam, quis nostrud exerci tation ullamcorper suscipit lobortis</p>
    <h3>INGREDIENTS</h3>
    <p>Lorem ipsum dolor sit amet, consectetuer adipiscing elit, sed diam nonummy nibh euismod tincidunt ut laoreet dolore magna</p>
  </div>
  <div class="about">
    <h4>ABOUT COMPANU</h4>
    <p>adipiscing elit, sed diam nonummy nibh euismod tincidunt ut laoreet dolore magna aliquam erat</p>
  </div>

  <div class="label-brand">
    <span class="dot"></span>
    <div><div class="name">Vorna</div><div class="sub">HEALTH SCIENCES</div></div>
  </div>

  <div class="product">
    <div class="product-name">CALM DRIFT</div>
    <div class="product-claim">ANXIETY AND STRESS</div>
  </div>

  <div class="facts">
    <h5>Nutrition Facts</h5>
    <div class="row" style="border:none"><span>Serving Size</span><span>...g</span></div>
    <div class="row thick"><span>Servings Per Container</span><span></span></div>
    <div class="row"><b>Amount Per Serving</b></div>
    <div class="row mid"><span><b>Calories</b> ....</span><span>Calories from Fat ...</span></div>
    <div class="row dv"><span>% Daily Value*</span></div>
    <div class="row"><span><b>Total Fat</b> ...g</span><b>...%</b></div>
    <div class="row indent"><span>Saturated Fat ...g</span><b>...%</b></div>
    <div class="row indent"><span><i>Trans</i> Fat ...g</span></div>
    <div class="row"><span><b>Cholestrol</b> ...mg</span><b>...%</b></div>
    <div class="row"><span><b>Sodium</b> ...mg</span><b>...%</b></div>
    <div class="row"><span><b>Total Carbohydrate</b> ...g</span><b>...%</b></div>
    <div class="row indent"><span>Dietary Fiber ...g</span><b>...%</b></div>
    <div class="row indent"><span>Sugars ...g</span></div>
    <div class="row thick"><span><b>Protein</b> ...g</span></div>
    <div class="row"><span>Vitamin A</span><b>...%</b></div>
    <div class="row"><span>Vitamin C</span><b>...%</b></div>
    <div class="row"><span>Calcium</span><b>...%</b></div>
    <div class="row mid"><span>Iron</span><b>...%</b></div>
    <div class="row note"><span>*Percent Daily Values are based on a 2,000 calorie diet. Your Daily Values may be higer or lower depending on your calorie needs.</span></div>
  </div>

  <div class="count">60 CAPSULES</div>
</section>

</body>
</html>
```